New Alcoholic Spiked Seltzer Line

We need a can design for a line of low calorie alcoholic seltzer. This product is a sparkling water and vodka drink with no sugar added in a slim 12 oz can.

This is a lighter, healthier, alternative to the sugary ready-to-drinks on the market. The product contains only 3 ingredients: Vodka, Water and Natural Flavors. It has only 100 calories but still has 5% alcohol, so you don't need to sacrifice alcohol to cut calories.

This product also does not contain any preservatives.

We want this design to communicate the following objectives to the consumer and in this order:

1. Appetizing product
2.Low calorie
3.Communicate the type of beverage (Spiked Seltzer)

The brand name of the product is VELKA.

The flavor of the product needed to be used for the design is Mango-Orange.

Comparable products are:

www.brindlefizzworks.example/
https://www.quorvabubbles.example
https://pelnavo.example/

The designs should not infringe or copy the creative directions of the products mentionned above. They are only given so that you can better understand the type of product we are developing.

Target Market(s)

Young Professional women between the ages of 25 and 44

Industry/Entity Type

Product

Colors

Designer to choose colors to be used in the design.

Requirements
Must have
• Design extendibility, meaning it can be adapted for other flavors.
• This is a new category in the market we are targeting, so consumers must easily be able to identify what type of product this is.

```html
<!DOCTYPE html>
<html lang="en">
<head>
<meta charset="UTF-8">
<title>VELKA Spiked Seltzer – Mango/Orange Can Label</title>
<link href="https://fonts.googleapis.com/css2?family=Josefin+Sans:wght@400;600&family=Work+Sans:wght@400;500;600&display=swap" rel="stylesheet">
<style>
  :root {
    --backdrop: #ececec;
    --label-white: #fbfbfb;
    --ink: #1c1c1c;
    --soft-ink: #4a4a4a;
    --citrus-yellow: #efd900;
    --mango-glow: #f9d65a;
    --orange-glow: #f7b548;
    --fruit-fade: #fdf6df;
  }
  * { margin: 0; padding: 0; box-sizing: border-box; }
  html, body {
    width: 1200px;
    height: 800px;
    overflow: hidden;
    background: var(--backdrop);
  }
  .canvas {
    position: relative;
    width: 1200px;
    height: 800px;
  }
  .can-label {
    position: absolute;
    left: 502px;
    top: 132px;
    width: 196px;
    height: 524px;
    background: var(--label-white);
    overflow: hidden;
    color: var(--ink);
    font-family: 'Work Sans', sans-serif;
  }
  .lid-band {
    position: absolute;
    left: 0; top: 0;
    width: 100%;
    height: 11px;
    background: var(--citrus-yellow);
  }
  .fruit-art {
    position: absolute;
    border-radius: 50%;
  }
  .fruit-art--mango {
    left: -8px;
    top: 56px;
    width: 72px;
    height: 118px;
    border-radius: 50% 50% 46% 54% / 56% 56% 44% 44%;
    background: radial-gradient(circle at 55% 40%, var(--mango-glow) 0%, var(--fruit-fade) 75%);
  }
  .fruit-art--orange {
    left: 138px;
    top: 240px;
    width: 104px;
    height: 112px;
    background: radial-gradient(circle at 38% 45%, var(--orange-glow) 0%, var(--fruit-fade) 75%);
  }
  .calorie-badge {
    position: absolute;
    left: 120px;
    top: 48px;
    display: flex;
    align-items: flex-start;
    gap: 4px;
  }
  .calorie-badge svg { margin-top: 2px; }
  .calorie-count {
    display: flex;
    flex-direction: column;
    align-items: center;
    line-height: 1;
  }
  .calorie-count__value {
    font-size: 15px;
    font-weight: 500;
    padding: 0 2px 2px;
    border-bottom: 1px solid var(--ink);
  }
  .calorie-count__unit {
    font-size: 10px;
    color: var(--soft-ink);
    margin-top: 2px;
  }
  .brand-name {
    position: absolute;
    left: 0; top: 190px;
    width: 100%;
    text-align: center;
    font-family: 'Josefin Sans', sans-serif;
    font-weight: 600;
    font-size: 34px;
    letter-spacing: 4px;
    line-height: 1;
  }
  .product-type {
    position: absolute;
    left: 65px;
    top: 272px;
    font-family: 'Josefin Sans', sans-serif;
    font-size: 15px;
    line-height: 20px;
    letter-spacing: 0.5px;
  }
  .flavor-tag {
    position: absolute;
    left: 36px;
    top: 367px;
    width: 117px;
    height: 26px;
    background: var(--citrus-yellow);
    font-size: 13.5px;
    font-weight: 600;
    line-height: 26px;
    text-align: center;
  }
  .abv-line {
    position: absolute;
    left: 0; top: 446px;
    width: 100%;
    display: flex;
    justify-content: center;
    align-items: center;
    gap: 5px;
    font-size: 10px;
    color: var(--soft-ink);
  }
  .abv-line__value {
    width: 25px;
    height: 25px;
    border-radius: 50%;
    background: var(--citrus-yellow);
    color: var(--ink);
    font-size: 12px;
    font-weight: 500;
    display: flex;
    align-items: center;
    justify-content: center;
  }
</style>
</head>
<body>
<main class="canvas">
  <section class="can-label" aria-label="VELKA spiked seltzer can label, mango/orange">
    <div class="lid-band"></div>

    <div class="fruit-art fruit-art--mango" role="img" aria-label="Line illustration of a ripe mango with stem and leaf"></div>

    <div class="calorie-badge">
      <svg width="14" height="26" viewBox="0 0 14 26" aria-hidden="true">
        <polygon points="8,0 1,14 6,14 4,26 13,10 8,10 11,0" fill="var(--citrus-yellow)"/>
      </svg>
      <div class="calorie-count">
        <span class="calorie-count__value">100</span>
        <span class="calorie-count__unit">calories</span>
      </div>
    </div>

    <h1 class="brand-name">VELKA</h1>

    <div class="fruit-art fruit-art--orange" role="img" aria-label="Line illustration of a fresh orange with leaf"></div>

    <p class="product-type">SPIKED<br>SELTZER</p>

    <p class="flavor-tag">mango/orange</p>

    <p class="abv-line">
      <span>•</span><span>ALC</span>
      <span class="abv-line__value">5.0</span>
      <span>VOL</span><span>•</span>
    </p>
  </section>
</main>
</body>
</html>
```